Harborline Lending and Capital. We provide MOSTLY residential home mortgages in Florida AND commercial loans for investment properties throughout the United states.
I would love to emulate so of the lender sites that are available on the internet but I would like to have the site as popular as possible for SEO purposes. Clients can already click the link to take them to the mortgage application where they can complete that and upload documents. If you could polish that up for me that would be great. I can also provide you with great detail on loan programs that are currently being offered. WE OFFER ALL MORTGAGE LENDING PRODUCTS. I would also like to add something in reference to the rate but I don't think it's legal to actually state or promise a rate for mortgage since they vary based on loan type, client and other criteria...

On the Harborline real estate site I would like to add a link or some way for clients to be able to put in credit card information to render services ...

Please let me know what you need from me

Thank you !!

Current link to site to improve and code

https://harborlinelendingandcapital.example/

Industry/Entity Type

Residential and commmercial lending

Coding

Coded - Design and coding required

Number of Pages Required

2 page

Requirements
Must have
• Love to integrate Mortgage interest rates even if general
Nice to have
• Link to fill out mortgage application via Quorvel LPX software

```html
<!DOCTYPE html>
<html lang="en">
<head>
<meta charset="utf-8">
<title>Harborline Lending and Capital</title>
<link href="https://fonts.googleapis.com/css2?family=Poppins:wght@400;500;600;700;800&display=swap" rel="stylesheet">
<style>
:root{
  --green:#8dbb3e;
  --green-dark:#1c3b20;
  --forest:#1d4427;
  --ink:#222;
  --muted:#3a3a3a;
  --band:#f4f4f4;
  --white:#fff;
}
*{box-sizing:border-box;margin:0;padding:0}
html,body{width:1200px;height:3690px;overflow:hidden}
body{font-family:"Poppins",sans-serif;color:var(--ink);background:var(--white);position:relative}
.abs{position:absolute}
.btn{position:absolute;background:var(--green);color:var(--white);font-weight:700;font-size:15px;letter-spacing:.5px;display:flex;align-items:center;justify-content:center;text-transform:uppercase}

/* header */
.site-header{position:absolute;left:0;top:0;width:1200px;height:95px;background:var(--white)}
.brand{position:absolute;left:75px;top:27px;display:flex;align-items:center;gap:12px}
.brand-mark{width:40px;height:40px;background:var(--green-dark)}
.brand-name{font-weight:700;font-size:14px;color:var(--green-dark);line-height:1.2}
.brand-name small{display:block;font-size:8px;font-weight:500;letter-spacing:2px}
.nav a{position:absolute;top:40px;font-size:14px;font-weight:600;color:#333;text-decoration:none;letter-spacing:.3px}
.nav .active{color:var(--green-dark);border-bottom:2px solid var(--green-dark);padding-bottom:3px}
.nav-cta{left:982px;top:24px;width:145px;height:49px;font-size:14px}

/* hero */
.hero{position:absolute;left:0;top:95px;width:1200px;height:624px;
  background:linear-gradient(180deg,#5c7d55 0%,#6b8a4a 40%,#7a8f4e 70%,#4f6e3a 100%)}
.hero-title{position:absolute;left:0;top:180px;width:1200px;text-align:center;color:var(--white);font-size:42px;font-weight:800;line-height:48px;text-transform:uppercase;text-shadow:0 2px 6px rgba(0,0,0,.35)}
.hero-sub{position:absolute;left:0;top:336px;width:1200px;text-align:center;color:var(--white);font-size:21px;text-shadow:0 1px 4px rgba(0,0,0,.4)}
.hero-cta{left:351px;top:387px;width:504px;height:48px;font-size:15px}
.dots{position:absolute;display:flex;gap:11px}
.dots span{width:9px;height:9px;background:var(--white)}
.dots span.on{background:var(--green)}
.dots.grey span{background:#999}
.dots.grey span.on{background:var(--green)}

/* section titles */
.ghost{position:absolute;left:0;width:1200px;text-align:center;font-weight:800;color:#efefef;text-transform:uppercase;letter-spacing:2px}
.sec-title{position:absolute;left:0;width:1200px;text-align:center;font-weight:800;color:var(--green-dark);text-transform:uppercase;font-size:38px;letter-spacing:1px}
.about-text{position:absolute;left:60px;top:870px;width:1080px;text-align:center;font-size:14.5px;line-height:27px;color:var(--muted)}

/* properties */
.properties{position:absolute;left:0;top:1136px;width:1200px;height:594px;background:var(--band)}
.card{position:absolute;top:202px;height:248px}
.card-center{position:absolute;left:419px;top:169px;width:358px;height:313px;background:var(--white);padding:5px;box-shadow:0 2px 10px rgba(0,0,0,.15)}
.card-center .photo{width:100%;height:100%;background:linear-gradient(160deg,#9ec3e8 0%,#e9ecef 35%,#d2d4d6 60%,#3a3d3e 100%);position:relative}
.card-label{position:absolute;left:0;bottom:0;width:100%;height:52px;background:rgba(28,59,32,.85);color:var(--white);font-size:18px;font-weight:500;display:flex;align-items:center;justify-content:center}

/* feature rows */
.feature-title{position:absolute;font-weight:800;color:var(--green-dark);font-size:38px;line-height:44px;text-transform:uppercase;letter-spacing:.5px}
.feature-text{position:absolute;font-size:14.5px;line-height:28px;color:var(--muted)}

/* rates band */
.rates{position:absolute;left:0;top:2281px;width:1200px;height:273px;overflow:hidden;
  background:linear-gradient(100deg,#8dbb3e 0%,#6f9c3a 45%,#2c5a2e 55%,#1d4427 100%)}
.rate-label{position:absolute;color:var(--white);font-weight:700;font-size:20px;line-height:28px;text-transform:uppercase}
.rate-value{position:absolute;color:var(--white);text-align:center;width:200px}
.rate-value b{display:block;font-size:58px;font-weight:800;line-height:60px}
.rate-value span{font-size:23px;font-weight:600}
.rate-mark{position:absolute;left:540px;top:63px;width:124px;height:124px;border:5px solid var(--white);border-radius:50%}

/* contact */
.contact-photo{position:absolute;left:0;top:3102px;width:587px;height:490px;background:linear-gradient(180deg,#9ab7c9 0%,#6f8a5a 45%,#3e3a32 65%,#5b8f3d 100%)}
.contact{position:absolute;left:587px;top:3102px;width:613px;height:490px;background:var(--green-dark)}
.contact h2{position:absolute;left:29px;top:52px;color:var(--white);font-size:38px;font-weight:700;text-transform:uppercase}
.contact p{position:absolute;left:29px;top:108px;color:var(--white);font-size:15px}
.field{position:absolute;background:var(--white);font-size:12px;color:#444;padding:0 14px;display:flex;align-items:center}
.field.area{align-items:flex-start;padding-top:14px}

/* footer */
.site-footer{position:absolute;left:0;top:3592px;width:1200px;height:98px;background:var(--white)}
.site-footer .copy{position:absolute;left:75px;top:44px;font-size:13px;color:#333}
.social{position:absolute;top:42px;width:20px;height:20px;border-radius:50%;background:var(--green-dark)}
.count{position:absolute;left:1166px;top:45px;font-size:13px;color:#333}
</style>
</head>
<body>

<header class="site-header">
  <div class="brand">
    <div class="brand-mark"></div>
    <div class="brand-name">Harborline Lending and Capital<small>BUSINESS AND COMMERCIAL DIVISION</small></div>
  </div>
  <nav class="nav">
    <a class="active" style="left:686px">HOME</a>
    <a style="left:772px">ABOUT</a>
    <a style="left:864px">PROPERTIES</a>
  </nav>
  <div class="btn nav-cta">Contact Us</div>
</header>

<section class="hero" role="img" aria-label="Aerial view of a green suburban neighbourhood with rows of houses">
  <h1 class="hero-title">Your best resource for<br>hassle-free, low cost mortgage<br>origination</h1>
  <p class="hero-sub">Residential home loans in florida and commercial lending in america.</p>
  <div class="btn hero-cta">Fill out mortgage application to begin lending pr</div>
  <div class="dots" style="left:568px;top:572px"><span class="on"></span><span></span><span></span><span></span></div>
</section>

<section class="about">
  <div class="ghost" style="top:758px;font-size:84px">Who we are</div>
  <h2 class="sec-title" style="top:790px">About Harborline Lending and Capital</h2>
  <p class="about-text">Harborline Originates Residential Home loans in Florida and Commercial and business financing in all 50 States.<br>We have over 25 years of experience in ALL types of real estate and commercial lending. We are strategically partnered to help you obtain<br>ALL necessary components of residential and commercial lending. From the RIGHT lending partners to the best practice Insurance<br>avenues and commercial and residential real estate partners.</p>
  <div class="btn" style="left:529px;top:1011px;width:144px;height:50px;font-size:14px">Read More</div>
</section>

<section class="properties">
  <div class="ghost" style="top:42px;font-size:90px;color:#e6e6e6">Properties</div>
  <h2 class="sec-title" style="top:72px">Available Properties</h2>
  <div class="card" style="left:0;width:100px;background:linear-gradient(90deg,#1e2a38,#c88a3a)" role="img" aria-label="Modern dark house exterior"></div>
  <div class="card" style="left:113px;width:291px;background:linear-gradient(170deg,#6fa6e0 0%,#b4643d 45%,#e8e6e2 65%,#6f9a48 100%)" role="img" aria-label="Modern house with wood cladding"></div>
  <div class="card-center">
    <div class="photo" role="img" aria-label="White modern house with large dark windows">
      <div class="card-label">12 Sunset Street</div>
    </div>
  </div>
  <div class="card" style="left:794px;width:291px;background:linear-gradient(180deg,#d9dde0 0%,#b08a62 45%,#2a9bc9 80%,#1c7fb0 100%)" role="img" aria-label="House with patio and swimming pool"></div>
  <div class="card" style="left:1097px;width:103px;background:linear-gradient(180deg,#5f93d8 0%,#e9e6df 55%,#c9c4bb 100%)" role="img" aria-label="Single storey house with driveway"></div>
  <div class="dots grey" style="left:566px;top:524px"><span class="on"></span><span></span><span></span><span></span></div>
</section>

<section class="loan-programs">
  <svg class="abs" style="left:66px;top:1803px" width="495" height="425" viewBox="0 0 495 425" role="img" aria-label="Hands using a calculator beside a small model house and paperwork">
    <defs><linearGradient id="lp" x1="0" y1="0" x2="1" y2="1"><stop offset="0" stop-color="#cfc7bf"/><stop offset=".5" stop-color="#b8a48e"/><stop offset="1" stop-color="#8c6a48"/></linearGradient></defs>
    <path d="M40 60 C70 10 140 0 200 20 C260 40 300 -10 370 15 C450 45 490 110 485 200 C480 300 420 380 330 405 C240 430 160 420 110 395 C60 370 95 300 70 240 C40 170 10 110 40 60Z" fill="url(#lp)"/>
    <path d="M5 110 C0 170 60 200 80 260 C100 330 60 380 110 412 C170 430 260 425 330 405" fill="none" stroke="#8dbb3e" stroke-width="6"/>
  </svg>
  <h2 class="feature-title" style="left:616px;top:1838px">Loan Programs</h2>
  <p class="feature-text" style="left:616px;top:1898px;width:510px">Sed ut perspiciatis unde omnis iste natus error sit voluptatem accusantium doloremque laudantium, totam rem aperiam, eaque ipsa quae ab illo inventore veritatis et quasi architecto beatae vitae dicta sunt explicabo. Nemo enim ipsam voluptatem quia voluptas sit aspernatur aut odit aut fugit, sed quia consequuntur magni dolores eos qui ratione voluptatem sequi nesciunt.</p>
  <div class="btn" style="left:616px;top:2126px;width:177px;height:49px">Read More</div>
</section>

<section class="rates" role="img" aria-label="Green tinted aerial neighbourhood backdrop">
  <svg class="abs" style="left:73px;top:74px" width="40" height="34" viewBox="0 0 40 34"><path d="M20 2 L38 18 H32 V32 H24 V22 H16 V32 H8 V18 H2Z" fill="#fff"/></svg>
  <div class="rate-label" style="left:73px;top:117px">Residential<br>home mortgages<br>rates</div>
  <div class="rate-value" style="left:321px;top:88px"><b>8.35%</b><span>Per Annum</span></div>
  <div class="rate-mark"></div>
  <svg class="abs" style="left:707px;top:74px" width="26" height="34" viewBox="0 0 26 34"><rect x="2" y="2" width="22" height="30" fill="none" stroke="#fff" stroke-width="3"/><rect x="8" y="8" width="4" height="4" fill="#fff"/><rect x="14" y="8" width="4" height="4" fill="#fff"/><rect x="8" y="15" width="4" height="4" fill="#fff"/><rect x="14" y="15" width="4" height="4" fill="#fff"/><rect x="10" y="23" width="6" height="9" fill="#fff"/></svg>
  <div class="rate-label" style="left:704px;top:117px">Commercial<br>loans for<br>investment rates</div>
  <div class="rate-value" style="left:937px;top:88px"><b>8.35%</b><span>Per Annum</span></div>
</section>

<section class="lending-products">
  <h2 class="feature-title" style="left:75px;top:2677px">Mortgage Lending<br>Products</h2>
  <p class="feature-text" style="left:75px;top:2780px;width:510px">Sed ut perspiciatis unde omnis iste natus error sit voluptatem accusantium doloremque laudantium, totam rem aperiam, eaque ipsa quae ab illo inventore veritatis et quasi architecto beatae vitae dicta sunt explicabo.</p>
  <div class="btn" style="left:75px;top:2917px;width:177px;height:50px">Read More</div>
  <svg class="abs" style="left:636px;top:2618px" width="495" height="425" viewBox="0 0 495 425" role="img" aria-label="Model house with coins, pen and calculator on paperwork">
    <defs><linearGradient id="mp" x1="0" y1="0" x2="1" y2="1"><stop offset="0" stop-color="#eceeef"/><stop offset=".55" stop-color="#c7cbcd"/><stop offset="1" stop-color="#5c6266"/></linearGradient></defs>
    <path d="M60 50 C130 10 230 30 290 15 C370 -5 470 30 488 110 C500 180 450 230 440 300 C430 380 350 420 250 412 C150 405 60 410 25 340 C-5 280 20 200 15 140 C10 90 30 65 60 50Z" fill="url(#mp)"/>
    <path d="M15 150 C0 230 10 330 60 375 C110 420 190 420 250 418 C330 416 390 400 420 360" fill="none" stroke="#8dbb3e" stroke-width="6"/>
  </svg>
</section>

<div class="contact-photo" role="img" aria-label="Modern two storey house with timber cladding beside a large tree"></div>
<section class="contact">
  <h2>Get in Touch</h2>
  <p>Please send me a message for general inquiries or reservations.</p>
  <div class="field" style="left:29px;top:144px;width:247px;height:49px">First Name</div>
  <div class="field" style="left:306px;top:144px;width:233px;height:49px">Last Name</div>
  <div class="field" style="left:29px;top:208px;width:247px;height:49px">Email Address</div>
  <div class="field" style="left:306px;top:208px;width:233px;height:49px">Phone No</div>
  <div class="field area" style="left:29px;top:272px;width:510px;height:94px">Message</div>
  <div class="btn" style="left:29px;top:383px;width:177px;height:49px">Submit</div>
</section>

<footer class="site-footer">
  <p class="copy">©2025 CompanyName. All rights reserved. Terms &amp; Conditions</p>
  <span class="social" style="left:957px" aria-label="Social link"></span>
  <span class="social" style="left:988px" aria-label="Social link"></span>
  <span class="social" style="left:1022px" aria-label="Social link"></span>
  <span class="social" style="left:1064px" aria-label="Social link"></span>
  <span class="social" style="left:1107px" aria-label="Social link"></span>
  <span class="count">x10</span>
</footer>

</body>
</html>
```